Business card design for holistic health care clinic

We need a double-sided business card design for our holistic health care clinic that integrates our logo design and also its color scheme. My business is called Valmira. It is an integrative medicine clinic. You have already done the logo for me. Please ensure an elegant and upscale design that is not cluttered, but still has all the necessary information (please see below for details).

Target Market(s)

Wellness, fitness, rehabilitation for educated, well-traveled open-minded clients who are focused on natural, organic, balanced and preventive healthcare and lifestyle.

Industry/Entity Type

Medical

Contact Information for Business Card

Modern, clean.

Number of Pages Required

1 page

Font styles to use
Serif
Sans Serif

Colors

Designer to choose colors to be used in the design.

Requirements
Must have
• Logo on one side, all other information on the other side.
• Other information should include:
• Tobias Wrenfeld - DOE, CPT, LMT
• 4100 East Marrow Drive
• Austin, TX 78119
• 512 555 0148
• 818 555 0192
• info@ValmiraHealth.example
• t.wrenfeld@ValmiraHealth.example
Nice to have
• Darker background on front - but not totally black - shaded/dark gray.

```html
<!DOCTYPE html>
<html lang="en">
<head>
<meta charset="utf-8">
<title>Valmira – Business Card</title>
<link rel="stylesheet" href="https://fonts.googleapis.com/css2?family=Quicksand:wght@400;500;700&display=swap">
<style>
  :root {
    --backdrop: #2f2a27;
    --card: #333333;
    --card-edge: #2a2a2a;
    --accent: #1b8fd2;
    --accent-soft: #1a7fba;
  }
  * { margin: 0; padding: 0; box-sizing: border-box; }
  html, body { width: 1200px; height: 780px; overflow: hidden; }
  body {
    background: var(--backdrop);
    font-family: "Quicksand", "Helvetica Neue", Arial, sans-serif;
    color: var(--accent);
    position: relative;
  }
  .card {
    position: absolute;
    top: 236px;
    width: 540px;
    height: 309px;
    background: var(--card);
    border: 1px solid var(--card-edge);
    box-shadow: 0 10px 30px rgba(0,0,0,.45);
    overflow: hidden;
  }
  .card--front { left: 40px; }
  .card--back { left: 620px; }

  .brand { position: absolute; text-align: left; }
  .brand__name {
    display: block;
    font-weight: 700;
    font-size: 56px;
    line-height: 1;
    letter-spacing: 1px;
    color: var(--accent);
  }
  .brand__tagline {
    display: block;
    margin-top: 6px;
    font-weight: 700;
    font-size: 14px;
    letter-spacing: .3px;
    color: var(--accent);
  }
  .card--front .brand { left: 250px; top: 150px; }
  .card--back .brand { left: 280px; top: 120px; }

  .holder { position: absolute; left: 0; top: 28px; display: flex; align-items: flex-start; }
  .holder__marker {
    width: 11px; height: 22px;
    background: var(--accent);
    border-radius: 0 11px 11px 0;
    margin-right: 16px;
    margin-top: 2px;
  }
  .holder__name { font-weight: 700; font-size: 17px; line-height: 1.1; text-transform: uppercase; }
  .holder__creds { font-weight: 400; font-size: 11px; letter-spacing: .5px; margin-top: 2px; }

  .rule {
    position: absolute; left: 22px; right: 22px; top: 228px;
    height: 1px; background: var(--accent-soft);
  }
  .contacts {
    position: absolute; left: 18px; right: 18px; top: 242px;
    display: flex; align-items: center;
    font-size: 11.5px; font-weight: 500; line-height: 1.6;
  }
  .contacts__group { padding: 0 12px; }
  .contacts__group + .contacts__group { border-left: 1px solid var(--accent-soft); }
  .contacts__item { display: flex; align-items: center; gap: 6px; white-space: nowrap; }
  .contacts__item svg { width: 13px; height: 13px; flex: none; }
  .contacts__address { font-size: 12px; line-height: 1.5; }
</style>
</head>
<body>
  <section class="card card--front" aria-label="Card front">
    <div class="brand">
      <span class="brand__name">VALMIRA</span>
      <span class="brand__tagline">Integrative Holistic Medicine</span>
    </div>
  </section>

  <section class="card card--back" aria-label="Card back">
    <div class="holder">
      <span class="holder__marker"></span>
      <div>
        <div class="holder__name">Tobias Wrenfeld</div>
        <div class="holder__creds">DOE, CPT, LMT</div>
      </div>
    </div>

    <div class="brand">
      <span class="brand__name">VALMIRA</span>
      <span class="brand__tagline">Integrative Holistic Medicine</span>
    </div>

    <div class="rule"></div>

    <div class="contacts">
      <div class="contacts__group">
        <div class="contacts__item">
          <svg viewBox="0 0 14 14" fill="none" stroke="currentColor" stroke-width="1.1"><circle cx="7" cy="7" r="6.2"/><rect x="5" y="3.5" width="4" height="7" rx=".7"/></svg>
          512 555 0148
        </div>
        <div class="contacts__item">
          <svg viewBox="0 0 14 14" fill="none" stroke="currentColor" stroke-width="1.1"><circle cx="7" cy="7" r="6.2"/><path d="M4.6 4.2c-.5 2.6 1.9 5.4 4.8 5.8l.6-1.3-1.3-.8-.6.6c-.9-.4-1.6-1.2-1.9-2l.6-.6-.8-1.3z"/></svg>
          818 555 0192
        </div>
      </div>
      <div class="contacts__group">
        <div class="contacts__item">
          <svg viewBox="0 0 14 14" fill="none" stroke="currentColor" stroke-width="1.1"><circle cx="7" cy="7" r="6.2"/><rect x="4" y="4.8" width="6" height="4.4"/><path d="M4 4.8l3 2.4 3-2.4"/></svg>
          info@ValmiraHealth.example
        </div>
        <div class="contacts__item">
          <svg viewBox="0 0 14 14" fill="none" stroke="currentColor" stroke-width="1.1"><circle cx="7" cy="7" r="6.2"/><rect x="4" y="4.8" width="6" height="4.4"/><path d="M4 4.8l3 2.4 3-2.4"/></svg>
          t.wrenfeld@ValmiraHealth.example
        </div>
      </div>
      <div class="contacts__group contacts__address">
        4100 East Marrow Drive<br>
        Austin, TX 78119
      </div>
    </div>
  </section>
</body>
</html>
```